Locksmith Services Tri Fold Flyer

We are a security company that provide all forms of security, we are looking to have tri fold flyers created for each service we offer starting with Locksmith Services, I am looking to work with someone who can design the layout and advise where the text would go where the pictures would go etc as well as tweaking our current logo, I am hoping to find someone that I can work with across all marketing materials for the business.

Our company is called Harbourline Venture Collective , and the Locksmith side will be Harbourline Keysmiths which is why the logo will need tweaking but with the text " Part of the Harbourline Venture Collective "

Logo Text

Our Strap Line is " Protecting People, Property & Assets "

```html
<!DOCTYPE html>
<html lang="en">
<head>
<meta charset="utf-8">
<title>Harbourline Keysmiths – Tri Fold Flyer</title>
<link href="https://fonts.googleapis.com/css2?family=Montserrat:wght@400;500;600;700;800&family=Poppins:ital,wght@1,700;1,800&display=swap" rel="stylesheet">
<style>
:root{
  --black:#0b0b0b;
  --gold:#c7a962;
  --gold-dark:#a98a45;
  --white:#ffffff;
  --ink:#1c1c1c;
  --grey:#e7e7e7;
  --line:#9a9a9a;
  --canvas:#ededed;
}
*{margin:0;padding:0;box-sizing:border-box}
html,body{width:1200px;height:2477px;overflow:hidden}
body{background:var(--canvas);font-family:"Montserrat",sans-serif;color:var(--ink)}
.spread{position:absolute;left:50px;width:1100px;height:776px;background:var(--white);overflow:hidden;box-shadow:0 10px 30px rgba(0,0,0,.25)}
.spread--outside{top:300px}
.spread--inside{top:1400px}
.shapes{position:absolute;left:0;top:0}
.abs{position:absolute}
.heading{font-weight:700;font-size:18px;line-height:1.15;color:var(--white);text-transform:uppercase}
.gold{color:var(--gold)}
.body-copy{font-size:9.6px;line-height:1.32;font-weight:400}
.body-copy--light{color:var(--white)}
.intro-lead{font-size:14px;line-height:1.12;font-weight:600}
.intro-lead strong{font-weight:700;color:var(--ink)}
.check-list{list-style:none}
.check-list li{display:flex;align-items:center;gap:10px;font-size:9.8px;line-height:1.2}
.check-list--dotted li{height:26.5px;border-bottom:1px dotted var(--line)}
.check-list--dotted li span{flex:1}
.tick{width:11px;height:11px;flex:none}
.hour-service{font-family:"Poppins",sans-serif;font-style:italic;font-weight:800;letter-spacing:-.5px;text-transform:uppercase;white-space:nowrap}
.hour-service .num{color:var(--white)}
.hour-service .word{color:var(--gold)}
.phone-number{font-weight:600;letter-spacing:.5px}
.strapline{font-weight:700;font-size:28px;line-height:1.05;text-transform:uppercase;color:var(--white);text-align:center}
.brand-name{font-weight:700;color:var(--gold);text-align:center;text-transform:uppercase;letter-spacing:1px}
.panel-label{position:absolute;top:162px;height:48px;display:flex;align-items:center;justify-content:center;gap:8px;font-weight:700;font-size:15px;text-transform:uppercase;color:var(--white)}
.panel-col{position:absolute;top:236px;width:310px}
.sub-heading{font-weight:700;font-size:15.5px;line-height:1.18;color:var(--gold);text-transform:uppercase;margin-top:18px}
.sub-lead{font-weight:700;font-size:12.5px;line-height:1.2;color:var(--ink);margin-top:2px}
.compact-list{margin-top:16px}
.compact-list li{font-size:8.6px;gap:8px;margin-bottom:10px;align-items:flex-start}
.compact-list--tight li{margin-bottom:9.4px}
.two-col{display:grid;grid-template-columns:1fr 1fr;column-gap:12px}
.perks{position:absolute;left:32px;top:592px;width:298px;height:140px;background:var(--grey);display:grid;grid-template-columns:1fr 1fr;align-items:center;justify-items:center;padding:10px 0}
.perk{display:flex;flex-direction:column;align-items:center;gap:4px;font-size:8px;color:var(--gold);text-transform:uppercase;font-weight:500}
.perk svg{width:26px;height:26px}
.pill{position:absolute;display:flex;align-items:center;background:var(--gold);border-radius:20px;color:var(--white);font-weight:600}
.pill .icon{width:40px;height:40px;border-radius:50%;background:var(--black);display:flex;align-items:center;justify-content:center;margin-left:-2px}
</style>
</head>
<body>

<section class="spread spread--outside" aria-label="Flyer outside spread">
  <svg class="shapes" width="1100" height="776" viewBox="0 0 1100 776">
    <defs>
      <linearGradient id="gWorkshop" x1="0" y1="0" x2="1" y2="1">
        <stop offset="0" stop-color="#1a1a1a"/><stop offset=".5" stop-color="#4b4134"/><stop offset="1" stop-color="#141414"/>
      </linearGradient>
      <linearGradient id="gDoor" x1="0" y1="0" x2="1" y2="0">
        <stop offset="0" stop-color="#3d3b44"/><stop offset=".45" stop-color="#8a6a55"/><stop offset="1" stop-color="#e4e2dd"/>
      </linearGradient>
      <linearGradient id="gKeys" x1="0" y1="0" x2="1" y2="0">
        <stop offset="0" stop-color="#2a2520"/><stop offset=".5" stop-color="#8a7a5c"/><stop offset="1" stop-color="#1c1a18"/>
      </linearGradient>
    </defs>
    <polygon points="0,0 1100,0 1100,237 870,237 750,424 372,424 250,237 0,237" fill="#0b0b0b"/>
    <g role="img" aria-label="Photo: locksmith smiling while working on a car ignition">
      <polygon points="330,0 860,0 860,237 745,410 378,410 330,340" fill="url(#gWorkshop)"/>
    </g>
    <polyline points="0,244 254,244 376,432 750,432 874,244 1100,244" fill="none" stroke="#c7a962" stroke-width="3"/>
    <g role="img" aria-label="Photo: locksmith fitting a lock into a white door">
      <polygon points="876,252 1100,252 1100,638 740,638 740,440" fill="url(#gDoor)"/>
    </g>
    <polyline points="1100,600 1075,638" fill="none" stroke="#c7a962" stroke-width="3"/>
    <rect x="0" y="638" width="1100" height="5" fill="#c7a962"/>
    <rect x="0" y="643" width="1100" height="133" fill="#0b0b0b"/>
    <g role="img" aria-label="Photo: hands cutting a key on a key machine">
      <rect x="0" y="643" width="300" height="127" fill="url(#gKeys)"/>
    </g>
    <polygon points="422,743 674,743 690,772 406,772" fill="#c7a962"/>
    <rect x="0" y="770" width="1100" height="6" fill="#c7a962"/>
  </svg>

  <div class="abs heading" style="left:32px;top:22px;">Quick and reliable<br><span class="gold">Emergency locksmith<br>service</span></div>
  <p class="abs body-copy body-copy--light" style="left:32px;top:100px;width:310px;">We know how stressful it is to be locked out of your home, break your ignition key, or deal with a break-in at the office. Our professional and skilled locksmiths are available 24/7 to handle any type of emergency, lock and key situation. You can count on Harbourline Keysmiths to get the job done quickly and efficiently, and we offer the most competitive rates in the industry backed by a Price Match Guarantee.</p>
  <p class="abs body-copy body-copy--light" style="left:32px;top:210px;width:310px;">We can handle any type of emergency locksmith situation and will always provide the highest level of customer service.</p>

  <p class="abs intro-lead gold" style="left:32px;top:265px;width:240px;">Our experienced professional locksmiths are <strong>trained to handle all types of emergency locksmith calls</strong></p>
  <ul class="abs check-list check-list--dotted" style="left:32px;top:352px;width:245px;">
    <li><svg class="tick" viewBox="0 0 12 12"><circle cx="6" cy="6" r="5.2" fill="none" stroke="#555" stroke-width="1"/><path d="M3.4 6.2l1.8 1.8 3.4-3.6" fill="none" stroke="#555" stroke-width="1.1"/></svg><span>24hr Emergency Lockouts / Openings</span></li>
    <li><svg class="tick" viewBox="0 0 12 12"><circle cx="6" cy="6" r="5.2" fill="none" stroke="#555" stroke-width="1"/><path d="M3.4 6.2l1.8 1.8 3.4-3.6" fill="none" stroke="#555" stroke-width="1.1"/></svg><span>Automobile / Car Entry</span></li>
    <li><svg class="tick" viewBox="0 0 12 12"><circle cx="6" cy="6" r="5.2" fill="none" stroke="#555" stroke-width="1"/><path d="M3.4 6.2l1.8 1.8 3.4-3.6" fill="none" stroke="#555" stroke-width="1.1"/></svg><span>Open Filing Cabinets</span></li>
    <li><svg class="tick" viewBox="0 0 12 12"><circle cx="6" cy="6" r="5.2" fill="none" stroke="#555" stroke-width="1"/><path d="M3.4 6.2l1.8 1.8 3.4-3.6" fill="none" stroke="#555" stroke-width="1.1"/></svg><span>Open Mailboxes locks</span></li>
    <li><svg class="tick" viewBox="0 0 12 12"><circle cx="6" cy="6" r="5.2" fill="none" stroke="#555" stroke-width="1"/><path d="M3.4 6.2l1.8 1.8 3.4-3.6" fill="none" stroke="#555" stroke-width="1.1"/></svg><span>Burglary / Break in Repairs</span></li>
    <li><svg class="tick" viewBox="0 0 12 12"><circle cx="6" cy="6" r="5.2" fill="none" stroke="#555" stroke-width="1"/><path d="M3.4 6.2l1.8 1.8 3.4-3.6" fill="none" stroke="#555" stroke-width="1.1"/></svg><span>Open locked car door / Trunk / fuel door</span></li>
    <li><svg class="tick" viewBox="0 0 12 12"><circle cx="6" cy="6" r="5.2" fill="none" stroke="#555" stroke-width="1"/><path d="M3.4 6.2l1.8 1.8 3.4-3.6" fill="none" stroke="#555" stroke-width="1.1"/></svg><span>Open locked / Stuck garage door</span></li>
    <li><svg class="tick" viewBox="0 0 12 12"><circle cx="6" cy="6" r="5.2" fill="none" stroke="#555" stroke-width="1"/><path d="M3.4 6.2l1.8 1.8 3.4-3.6" fill="none" stroke="#555" stroke-width="1.1"/></svg><span>Open automatic driveway gates</span></li>
    <li><svg class="tick" viewBox="0 0 12 12"><circle cx="6" cy="6" r="5.2" fill="none" stroke="#555" stroke-width="1"/><path d="M3.4 6.2l1.8 1.8 3.4-3.6" fill="none" stroke="#555" stroke-width="1.1"/></svg><span>Open / Repair any type of safe</span></li>
    <li><svg class="tick" viewBox="0 0 12 12"><circle cx="6" cy="6" r="5.2" fill="none" stroke="#555" stroke-width="1"/><path d="M3.4 6.2l1.8 1.8 3.4-3.6" fill="none" stroke="#555" stroke-width="1.1"/></svg><span>Open High security locks</span></li>
  </ul>

  <svg class="abs" style="left:536px;top:340px;" width="28" height="22" viewBox="0 0 28 22"><circle cx="14" cy="12" r="9" fill="none" stroke="#fff" stroke-width="2"/><path d="M14 7v5l3 2" fill="none" stroke="#fff" stroke-width="2"/></svg>
  <div class="abs hour-service" style="left:400px;top:358px;width:320px;text-align:center;font-size:34px;"><span class="num">24/7</span> <span class="word">Hour Service</span></div>

  <div class="abs brand-name" style="left:420px;top:470px;width:280px;font-size:16px;color:#e2d4b0;">Harbourline Keysmiths</div>
  <div class="abs" style="left:420px;top:496px;width:280px;text-align:center;font-size:10px;color:#e2d4b0;letter-spacing:1px;text-transform:uppercase;">Protecting People, Property &amp; Assets</div>
  <svg class="abs" style="left:548px;top:567px;" width="24" height="24" viewBox="0 0 24 24"><circle cx="12" cy="12" r="12" fill="#0b0b0b"/><path d="M8 6.5c.6-.5 1.4-.4 1.8.2l1 1.6c.3.5.2 1.1-.2 1.5l-.7.6c.6 1.4 1.6 2.5 3 3.1l.6-.7c.4-.4 1-.5 1.5-.2l1.6 1c.6.4.7 1.2.2 1.8l-.8.9c-.7.7-1.8.8-2.7.3-2.6-1.3-4.6-3.4-5.9-6-.4-.9-.3-2 .4-2.7z" fill="#fff"/></svg>
  <div class="abs phone-number" style="left:430px;top:594px;width:260px;text-align:center;font-size:26px;">0808-157-0147</div>

  <svg class="abs" style="left:550px;top:650px;" width="20" height="20" viewBox="0 0 20 20"><circle cx="10" cy="10" r="9" fill="none" stroke="#fff" stroke-width="1.5"/><rect x="5.5" y="6.5" width="9" height="7" rx="1" fill="#fff"/><path d="M5.5 7l4.5 3.5L14.5 7" fill="none" stroke="#0b0b0b" stroke-width="1"/></svg>
  <div class="abs" style="left:400px;top:676px;width:320px;text-align:center;font-size:11px;color:#fff;">hello@HarbourlineKeysmiths.com</div>
  <svg class="abs" style="left:550px;top:702px;" width="20" height="20" viewBox="0 0 20 20"><circle cx="10" cy="10" r="9" fill="none" stroke="#fff" stroke-width="1.5"/><circle cx="10" cy="10" r="5" fill="none" stroke="#fff" stroke-width="1.2"/><path d="M5 10h10M10 5c-2 3-2 7 0 10M10 5c2 3 2 7 0 10" fill="none" stroke="#fff" stroke-width="1"/></svg>
  <div class="abs" style="left:406px;top:750px;width:284px;text-align:center;font-size:10.5px;color:#111;">www.HarbourlineKeysmiths.com</div>

  <div class="abs" style="left:760px;top:30px;width:320px;text-align:center;">
    <div class="brand-name" style="font-size:24px;">Harbourline Keysmiths</div>
    <div style="margin-top:8px;font-size:9px;color:var(--gold);letter-spacing:1px;text-transform:uppercase;">Part of the Harbourline Venture Collective</div>
  </div>

  <div class="abs strapline" style="left:760px;top:660px;width:330px;">Protecting People<br><span class="gold">Property &amp; Assets</span></div>
  <div class="abs" style="left:760px;top:722px;width:330px;text-align:center;font-size:17px;color:#fff;">www.HarbourlineKeysmiths.com</div>
</section>

<section class="spread spread--inside" aria-label="Flyer inside spread">
  <svg class="shapes" width="1100" height="776" viewBox="0 0 1100 776">
    <defs>
      <linearGradient id="gDoorLock" x1="0" y1="0" x2="1" y2="0">
        <stop offset="0" stop-color="#2c2623"/><stop offset=".5" stop-color="#b07a4c"/><stop offset="1" stop-color="#c98d5a"/>
      </linearGradient>
      <linearGradient id="gCar" x1="0" y1="0" x2="1" y2="1">
        <stop offset="0" stop-color="#4a5260"/><stop offset=".6" stop-color="#9c8a6c"/><stop offset="1" stop-color="#2f3540"/>
      </linearGradient>
      <linearGradient id="gFobs" x1="0" y1="0" x2="1" y2="0">
        <stop offset="0" stop-color="#8c88b8"/><stop offset=".5" stop-color="#3a3c52"/><stop offset="1" stop-color="#9591c0"/>
      </linearGradient>
    </defs>
    <g role="img" aria-label="Photo: hand turning a key in a wooden front door lock"><rect x="0" y="0" width="367" height="162" fill="url(#gDoorLock)"/></g>
    <g role="img" aria-label="Photo: locksmith opening a car door lock"><rect x="367" y="0" width="366" height="162" fill="url(#gCar)"/></g>
    <g role="img" aria-label="Photo: row of car key fobs on a purple surface"><rect x="733" y="0" width="367" height="162" fill="url(#gFobs)"/></g>
    <polygon points="368,0 732,0 712,50 388,50" fill="#c7a962"/>
    <rect x="0" y="162" width="1100" height="48" fill="#0b0b0b"/>
    <polygon points="386,172 714,172 736,216 364,216" fill="#ffffff"/>
    <rect x="0" y="756" width="1100" height="20" fill="#0b0b0b"/>
    <polygon points="382,731 718,731 740,776 360,776" fill="#0b0b0b"/>
  </svg>
  <div class="abs" style="left:368px;top:6px;width:364px;text-align:center;font-weight:700;font-size:28px;color:#fff;">OUR SERVICES</div>

  <div class="panel-label" style="left:0;width:367px;">
    <svg width="18" height="20" viewBox="0 0 18 20"><rect x="2" y="4" width="14" height="16" fill="#c7a962"/><rect x="5" y="0" width="8" height="5" fill="#c7a962"/><g fill="#0b0b0b"><rect x="4.5" y="7" width="2.5" height="2.5"/><rect x="11" y="7" width="2.5" height="2.5"/><rect x="4.5" y="12" width="2.5" height="2.5"/><rect x="11" y="12" width="2.5" height="2.5"/><rect x="7.5" y="16" width="3" height="4"/></g></svg>
    Residential
  </div>
  <div class="panel-label" style="left:367px;width:366px;top:172px;height:44px;color:#0b0b0b;">
    <svg width="26" height="20" viewBox="0 0 26 20"><path d="M4 9l3-6h12l3 6h2v8h-3v3h-3v-3H8v3H5v-3H2V9z" fill="#0b0b0b"/><circle cx="7" cy="12.5" r="1.6" fill="#fff"/><circle cx="19" cy="12.5" r="1.6" fill="#fff"/></svg>
    Automotive
  </div>
  <div class="panel-label" style="left:733px;width:367px;">
    <svg width="20" height="20" viewBox="0 0 20 20"><path d="M5 15V9a5 5 0 0110 0v6z" fill="#c7a962"/><rect x="3" y="15" width="14" height="3" fill="#c7a962"/><path d="M10 1v2M2 6l2 1M18 6l-2 1" stroke="#c7a962" stroke-width="1.5"/></svg>
    Emergency Locksmith
  </div>

  <div class="panel-col" style="left:28px;">
    <p class="body-copy">We know how stressful it is to be locked out of your home, break your ignition key, or deal with a break-in at the office. Our professional and skilled locksmiths are available 24/7 to handle any type of emergency, lock and key situation. You can count on Harbourline Keysmiths to get the job done quickly and efficiently, and we offer the most competitive rates in the industry backed by a Price Match Guarantee.</p>
    <h3 class="sub-heading">Services to protect your home &amp; family</h3>
    <p class="sub-lead">Deadbolts, Lock Rekeying &amp; Replacement, Door &amp; Cabinet Locks</p>
    <ul class="check-list compact-list two-col">
      <li><svg class="tick" viewBox="0 0 12 12"><circle cx="6" cy="6" r="5.2" fill="none" stroke="#c7a962"/><path d="M3.4 6.2l1.8 1.8 3.4-3.6" fill="none" stroke="#c7a962"/></svg>Deadbolt installation</li>
      <li><svg class="tick" viewBox="0 0 12 12"><circle cx="6" cy="6" r="5.2" fill="none" stroke="#c7a962"/><path d="M3.4 6.2l1.8 1.8 3.4-3.6" fill="none" stroke="#c7a962"/></svg>Patio door bars</li>
      <li><svg class="tick" viewBox="0 0 12 12"><circle cx="6" cy="6" r="5.2" fill="none" stroke="#c7a962"/><path d="M3.4 6.2l1.8 1.8 3.4-3.6" fill="none" stroke="#c7a962"/></svg>Rekeying existing locks and deadbolts</li>
      <li><svg class="tick" viewBox="0 0 12 12"><circle cx="6" cy="6" r="5.2" fill="none" stroke="#c7a962"/><path d="M3.4 6.2l1.8 1.8 3.4-3.6" fill="none" stroke="#c7a962"/></svg>Jimmy proof locks</li>
      <li><svg class="tick" viewBox="0 0 12 12"><circle cx="6" cy="6" r="5.2" fill="none" stroke="#c7a962"/><path d="M3.4 6.2l1.8 1.8 3.4-3.6" fill="none" stroke="#c7a962"/></svg>Gate, garage, and fencing locks</li>
      <li><svg class="tick" viewBox="0 0 12 12"><circle cx="6" cy="6" r="5.2" fill="none" stroke="#c7a962"/><path d="M3.4 6.2l1.8 1.8 3.4-3.6" fill="none" stroke="#c7a962"/></svg>Key cabinets and storage boxes</li>
      <li><svg class="tick" viewBox="0 0 12 12"><circle cx="6" cy="6" r="5.2" fill="none" stroke="#c7a962"/><path d="M3.4 6.2l1.8 1.8 3.4-3.6" fill="none" stroke="#c7a962"/></svg>Pushbutton locks</li>
      <li><svg class="tick" viewBox="0 0 12 12"><circle cx="6" cy="6" r="5.2" fill="none" stroke="#c7a962"/><path d="M3.4 6.2l1.8 1.8 3.4-3.6" fill="none" stroke="#c7a962"/></svg>Digital deadbolts</li>
      <li><svg class="tick" viewBox="0 0 12 12"><circle cx="6" cy="6" r="5.2" fill="none" stroke="#c7a962"/><path d="M3.4 6.2l1.8 1.8 3.4-3.6" fill="none" stroke="#c7a962"/></svg>Mortise locks</li>
      <li><svg class="tick" viewBox="0 0 12 12"><circle cx="6" cy="6" r="5.2" fill="none" stroke="#c7a962"/><path d="M3.4 6.2l1.8 1.8 3.4-3.6" fill="none" stroke="#c7a962"/></svg>Lever locks</li>
    </ul>
  </div>
  <div class="perks">
    <div class="perk"><svg viewBox="0 0 26 26"><rect x="2" y="8" width="13" height="10" fill="#111"/><path d="M15 11h5l4 4v3h-9z" fill="#111"/><circle cx="7" cy="20" r="2.5" fill="#111"/><circle cx="19" cy="20" r="2.5" fill="#111"/></svg>Express Service</div>
    <div class="perk"><svg viewBox="0 0 26 26"><circle cx="13" cy="11" r="8" fill="#111"/><path d="M9 11l3 3 5-6" fill="none" stroke="#fff" stroke-width="2"/><path d="M8 18l-2 6 4-2 3 2M18 18l2 6-4-2" fill="#111"/></svg>Price Match Guarantee</div>
    <div class="perk"><svg viewBox="0 0 26 26"><path d="M5 14a8 8 0 0116 0" fill="none" stroke="#111" stroke-width="2.4"/><rect x="3" y="13" width="4" height="7" rx="1.5" fill="#111"/><rect x="19" y="13" width="4" height="7" rx="1.5" fill="#111"/><circle cx="13" cy="15" r="3.5" fill="#111"/></svg>Free Consultation</div>
    <div class="perk"><svg viewBox="0 0 26 26"><path d="M7 4c.9-.7 2.1-.6 2.7.3l1.5 2.4c.4.7.3 1.6-.3 2.2l-1 .9c.9 2.1 2.4 3.7 4.5 4.6l.9-1c.6-.6 1.5-.7 2.2-.3l2.4 1.5c.9.6 1 1.8.3 2.7l-1.2 1.3c-1 1-2.7 1.2-4 .5-3.9-2-6.9-5.1-8.9-9-.6-1.3-.4-3 .6-4z" fill="#111"/></svg>$0.00 Service Call</div>
  </div>

  <div class="panel-col" style="left:395px;">
    <p class="body-copy">We know how stressful it is to be locked out of your home, break your ignition key, or deal with a break-in at the office. Our professional and skilled locksmiths are available 24/7 to handle any type of emergency, lock and key situation. You can count on Harbourline Keysmiths to get the job done quickly and efficiently, and we offer the most competitive rates in the industry backed by a Price Match Guarantee.</p>
    <h3 class="sub-heading">Car key replacement &amp; duplication services</h3>
    <p class="sub-lead">Harbourline Keysmiths offers the following automotive key services:</p>
    <ul class="check-list compact-list compact-list--tight">
      <li><svg class="tick" viewBox="0 0 12 12"><circle cx="6" cy="6" r="5.2" fill="none" stroke="#c7a962"/><path d="M3.4 6.2l1.8 1.8 3.4-3.6" fill="none" stroke="#c7a962"/></svg>Transponder (remote and key FOB) replacement</li>
      <li><svg class="tick" viewBox="0 0 12 12"><circle cx="6" cy="6" r="5.2" fill="none" stroke="#c7a962"/><path d="M3.4 6.2l1.8 1.8 3.4-3.6" fill="none" stroke="#c7a962"/></svg>Transponder chip repair, duplication, and replacement</li>
      <li><svg class="tick" viewBox="0 0 12 12"><circle cx="6" cy="6" r="5.2" fill="none" stroke="#c7a962"/><path d="M3.4 6.2l1.8 1.8 3.4-3.6" fill="none" stroke="#c7a962"/></svg>Smart and Flip Blade key repair or replacement</li>
      <li><svg class="tick" viewBox="0 0 12 12"><circle cx="6" cy="6" r="5.2" fill="none" stroke="#c7a962"/><path d="M3.4 6.2l1.8 1.8 3.4-3.6" fill="none" stroke="#c7a962"/></svg>VAT key copying</li>
      <li><svg class="tick" viewBox="0 0 12 12"><circle cx="6" cy="6" r="5.2" fill="none" stroke="#c7a962"/><path d="M3.4 6.2l1.8 1.8 3.4-3.6" fill="none" stroke="#c7a962"/></svg>VIN key copying</li>
      <li><svg class="tick" viewBox="0 0 12 12"><circle cx="6" cy="6" r="5.2" fill="none" stroke="#c7a962"/><path d="M3.4 6.2l1.8 1.8 3.4-3.6" fill="none" stroke="#c7a962"/></svg>PROX Car Key duplication and replacement</li>
      <li><svg class="tick" viewBox="0 0 12 12"><circle cx="6" cy="6" r="5.2" fill="none" stroke="#c7a962"/><path d="M3.4 6.2l1.8 1.8 3.4-3.6" fill="none" stroke="#c7a962"/></svg>Immobilizer key reprogramming</li>
      <li><svg class="tick" viewBox="0 0 12 12"><circle cx="6" cy="6" r="5.2" fill="none" stroke="#c7a962"/><path d="M3.4 6.2l1.8 1.8 3.4-3.6" fill="none" stroke="#c7a962"/></svg>Car remote programming</li>
      <li><svg class="tick" viewBox="0 0 12 12"><circle cx="6" cy="6" r="5.2" fill="none" stroke="#c7a962"/><path d="M3.4 6.2l1.8 1.8 3.4-3.6" fill="none" stroke="#c7a962"/></svg>Ignition switch repair and unlocking</li>
      <li><svg class="tick" viewBox="0 0 12 12"><circle cx="6" cy="6" r="5.2" fill="none" stroke="#c7a962"/><path d="M3.4 6.2l1.8 1.8 3.4-3.6" fill="none" stroke="#c7a962"/></svg>Broken key removal</li>
      <li><svg class="tick" viewBox="0 0 12 12"><circle cx="6" cy="6" r="5.2" fill="none" stroke="#c7a962"/><path d="M3.4 6.2l1.8 1.8 3.4-3.6" fill="none" stroke="#c7a962"/></svg>Car trunk opening</li>
      <li><svg class="tick" viewBox="0 0 12 12"><circle cx="6" cy="6" r="5.2" fill="none" stroke="#c7a962"/><path d="M3.4 6.2l1.8 1.8 3.4-3.6" fill="none" stroke="#c7a962"/></svg>High Security Car Key Cutting</li>
    </ul>
  </div>
  <div class="abs" style="left:382px;top:750px;width:336px;text-align:center;font-size:11px;color:#fff;">www.HarbourlineKeysmiths.com</div>

  <div class="panel-col" style="left:762px;">
    <p class="body-copy">We know how stressful it is to be locked out of your home, break your ignition key, or deal with a break-in at the office. Our professional and skilled locksmiths are available 24/7 to handle any type of emergency, lock and key situation. You can count on Harbourline Keysmiths to get the job done quickly and efficiently, and we offer the most competitive rates in the industry backed by a Price Match Guarantee.</p>
    <h3 class="sub-heading">We offer the following emergency locksmith services</h3>
    <ul class="check-list compact-list">
      <li><svg class="tick" viewBox="0 0 12 12"><circle cx="6" cy="6" r="5.2" fill="none" stroke="#c7a962"/><path d="M3.4 6.2l1.8 1.8 3.4-3.6" fill="none" stroke="#c7a962"/></svg>Emergency Lockout Services for Homes, Commercial Buildings, and Vehicles</li>
      <li><svg class="tick" viewBox="0 0 12 12"><circle cx="6" cy="6" r="5.2" fill="none" stroke="#c7a962"/><path d="M3.4 6.2l1.8 1.8 3.4-3.6" fill="none" stroke="#c7a962"/></svg>Lock Changes and Repair</li>
      <li><svg class="tick" viewBox="0 0 12 12"><circle cx="6" cy="6" r="5.2" fill="none" stroke="#c7a962"/><path d="M3.4 6.2l1.8 1.8 3.4-3.6" fill="none" stroke="#c7a962"/></svg>Re-Keying</li>
      <li><svg class="tick" viewBox="0 0 12 12"><circle cx="6" cy="6" r="5.2" fill="none" stroke="#c7a962"/><path d="M3.4 6.2l1.8 1.8 3.4-3.6" fill="none" stroke="#c7a962"/></svg>Keyless Entry Systems</li>
      <li><svg class="tick" viewBox="0 0 12 12"><circle cx="6" cy="6" r="5.2" fill="none" stroke="#c7a962"/><path d="M3.4 6.2l1.8 1.8 3.4-3.6" fill="none" stroke="#c7a962"/></svg>Master Key Systems</li>
      <li><svg class="tick" viewBox="0 0 12 12"><circle cx="6" cy="6" r="5.2" fill="none" stroke="#c7a962"/><path d="M3.4 6.2l1.8 1.8 3.4-3.6" fill="none" stroke="#c7a962"/></svg>Panic Bar Repair and Installation</li>
      <li><svg class="tick" viewBox="0 0 12 12"><circle cx="6" cy="6" r="5.2" fill="none" stroke="#c7a962"/><path d="M3.4 6.2l1.8 1.8 3.4-3.6" fill="none" stroke="#c7a962"/></svg>Access Control Systems</li>
    </ul>
  </div>
  <svg class="abs" style="left:790px;top:592px;" width="30" height="22" viewBox="0 0 30 22"><circle cx="15" cy="12" r="9" fill="none" stroke="#444" stroke-width="1.6"/><path d="M15 7v5l3 2" fill="none" stroke="#444" stroke-width="1.6"/></svg>
  <div class="abs hour-service" style="left:762px;top:606px;font-size:32px;"><span class="num" style="color:#1c1c1c;">24/7</span> <span class="word">Hour Service</span></div>
  <div class="abs" style="left:762px;top:654px;font-size:21px;font-weight:500;">For Emergency Services</div>
  <div class="pill" style="left:762px;top:690px;width:302px;height:40px;font-size:28px;">
    <span class="icon"><svg width="22" height="22" viewBox="0 0 24 24"><circle cx="12" cy="12" r="10" fill="none" stroke="#fff" stroke-width="1.4"/><path d="M8 6.5c.6-.5 1.4-.4 1.8.2l1 1.6c.3.5.2 1.1-.2 1.5l-.7.6c.6 1.4 1.6 2.5 3 3.1l.6-.7c.4-.4 1-.5 1.5-.2l1.6 1c.6.4.7 1.2.2 1.8l-.8.9c-.7.7-1.8.8-2.7.3-2.6-1.3-4.6-3.4-5.9-6-.4-.9-.3-2 .4-2.7z" fill="#fff"/></svg></span>
    <span style="flex:1;text-align:center;">0808-157-0147</span>
  </div>
</section>

</body>
</html>
```